Guided Study Tour - Klangtage Wendorf Two Sided Flyer

We need a two-sided flyer for a Guided Study Tour to Klangtage Wendorf. We want beautiful pictures of Germany and if possible some of the Halbig venues our participants will be visiting. I have also provided the content that needs to be included. Also, in the attached document I provided a link to the Klangtage event. Please read and watch the video to be inspired.
This flyer should be beautiful and engaging. It needs to grab your attention right away and really highlight the wonderful things that they will be doing and that are included in the tour. This is a once in a lifetime opportunity for people to experience. We are targeting Music Directors and Music professionals.
Both attached logos need to be present on the flyer.

```html
<!DOCTYPE html>
<html lang="en">
<head>
<meta charset="utf-8">
<title>Guided Study Tour – Klangtage Wendorf</title>
<link rel="stylesheet" href="https://fonts.googleapis.com/css2?family=Zilla+Slab:ital,wght@1,500&family=Cormorant+Garamond:wght@500;600&family=Allura&display=swap">
<style>
  :root {
    --slate: #2a2c2e;
    --slate-light: #36393b;
    --lime: #b9ff00;
    --ink: #1d1f1f;
    --paper: #e9e6df;
    --rule: #d8d6d0;
  }
  * { margin: 0; padding: 0; box-sizing: border-box; }
  html, body { width: 800px; height: 1200px; overflow: hidden; background: var(--slate); }
  .flyer {
    position: relative; width: 800px; height: 1200px; overflow: hidden;
    background: radial-gradient(ellipse at 40% 50%, var(--slate-light), var(--slate) 75%);
    color: var(--paper);
    font-family: "Cormorant Garamond", Georgia, serif;
  }
  .intro {
    position: absolute; left: 0; top: 47px; width: 370px; height: 313px;
    background: var(--lime); color: var(--ink);
    padding: 26px 0 0 67px;
    font-family: "Zilla Slab", Georgia, serif; font-style: italic; font-weight: 500;
    font-size: 21.5px; line-height: 23.5px; white-space: nowrap;
  }
  .photo { position: absolute; top: 45px; height: 315px; }
  .photo--hall { left: 376px; width: 206px;
    background: linear-gradient(180deg, #6fb3e0 0%, #cfe6dc 35%, #b9d9cf 65%, #7a5a3c 100%); }
  .photo--square { left: 588px; width: 212px;
    background: linear-gradient(180deg, #a9c3de 0%, #c9b39a 40%, #7a5a48 60%, #2b2630 100%); }
  .inclusions { position: absolute; left: 72px; top: 386px; width: 700px;
    font-size: 21px; line-height: 28.3px; white-space: nowrap; }
  .inclusions h2 { font-weight: 500; font-size: 21px; letter-spacing: .3px; }
  .inclusions ul { list-style: none; }
  .inclusions li { position: relative; padding-left: 17px; }
  .inclusions li::before { content: "\2731"; position: absolute; left: 0; top: 0; font-size: 12px; font-weight: 600; }
  .contact { position: absolute; left: 72px; top: 853px; font-size: 21px; white-space: nowrap; }
  .contact strong { font-weight: 600; }
  .contact em { font-family: "Zilla Slab", Georgia, serif; font-weight: 500; font-size: 19px; }
  .rule { position: absolute; left: 75px; width: 650px; height: 1px; background: var(--rule); }
  .rule--top { top: 914px; }
  .rule--bottom { top: 1142px; }
  .bio-title { position: absolute; left: 0; top: 920px; width: 800px; text-align: center;
    font-family: "Allura", cursive; font-weight: 400; font-size: 44px; line-height: 44px; color: var(--lime); }
  .bio-text { position: absolute; left: 20px; top: 964px; width: 760px; text-align: center;
    font-size: 18.5px; line-height: 21.2px; white-space: nowrap; }
</style>
</head>
<body>
<main class="flyer">
  <section class="intro">
    Daniel Marsh partnered with<br>
    Meridian Heritage Tours &amp;<br>
    Music Festivals to bring you<br>
    and experience of a Lifetime.<br>
    With over 100 years of<br>
    combined educational student<br>
    travel expertise, Meridian<br>
    Heritage Tours, powered<br>
    by Halden Tours, brings<br>
    unparalleled tour experiences<br>
    for you and your students.
  </section>
  <div class="photo photo--hall" role="img" aria-label="Photo of an ornate concert hall with a painted sky ceiling and chandeliers"></div>
  <div class="photo photo--square" role="img" aria-label="Photo of a crowded festival square in front of a historic town hall at dusk"></div>

  <section class="inclusions">
    <h2>TRIP INCLUSIONS</h2>
    <ul>
      <li>Roundtrip Airfare from Houston</li>
      <li>13 Nights Accomodations, 3 Star Hotels with A/C</li>
      <li>Daily Breakfast</li>
      <li>Access to rehearsal sessions</li>
      <li>Pirvate Luxury Coach Transfer Services for airport transfers and day tours<br>to Berlin, Weimar and Dresden &amp; Prague.</li>
      <li>Professional Local Guides for for City Tours in: Berlin, Weimar, Dresden &amp;<br>Prague</li>
      <li>Entrance Fees to: House of Anton Reiher, Emil Valden, Ottmar Siel in Weimar,<br>Lutheran Marienhallkirche &amp; Old Masters Gallery in the Westerling Palace in<br>Dresend, and Cathedral and Copper Lane in Prague</li>
      <li>All Applicable Taxes and Gratuities for Included Services, Guides, and<br>Drivers</li>
      <li>$2 Million in Professional Liability Insurance</li>
      <li>24-hour Travel Support Staff</li>
    </ul>
  </section>

  <p class="contact">For more information contact <strong>Dr. Marsh</strong> at <em>daniel.marsh@southernvalleystate.edu</em></p>

  <div class="rule rule--top"></div>
  <h2 class="bio-title">Daniel Marsh Bio:</h2>
  <p class="bio-text">
    Daniel Marsh is Director of Choral Studies at Southern Valley State<br>
    University and the conductor of the Lakeside Symphony Chorale and<br>
    the Lakeside Choral Artists, a professional chamber choir. A native Texan, his degrees<br>
    are from Harlan Pierce University, Brookmoor University and the University of the<br>
    Pacific Coast. Recent engagements include conducting the Harwell Requiem in Buffalo, NY,<br>
    serving on the jury for the Kalamos International Choral Festival in Kalamos, Greece and<br>
    the International Choir Championship CantoVivo in Mostar, Bosnia and Herzogevina.
  </p>
  <div class="rule rule--bottom"></div>
</main>
</body>
</html>
```